Veldmark Supplies Business Card

Professional business card that stand out to our potential customers. Front and back with clean modern design

Industry/Entity Type

Oil and gas

Contact Information for Business Card

Name, address, website , office phone and cell number

Requirements
Must have
• Editable files for each employee

```html
<!DOCTYPE html>
<html lang="en">
<head>
<meta charset="utf-8">
<title>Veldmark Supplies Business Card</title>
<link rel="stylesheet" href="https://fonts.googleapis.com/css2?family=Montserrat:wght@400;500;700;800&display=swap">
<style>
  :root {
    --stage: #1b1b1c;
    --card: #2b2b2d;
    --card-edge: #333336;
    --red: #e5232b;
    --blue: #1fa8d6;
    --text: #f2f2f2;
    --silver: #d4d4d6;
    --steel: #8a8a8d;
    --graphite: #3c3c3f;
    --black: #0a0a0b;
  }
  * { box-sizing: border-box; margin: 0; padding: 0; }
  html, body { width: 1200px; height: 689px; overflow: hidden; }
  body {
    background: var(--stage);
    font-family: "Montserrat", sans-serif;
    color: var(--text);
    position: relative;
  }
  .card {
    position: absolute;
    top: 190px;
    width: 540px;
    height: 309px;
    border-radius: 18px;
    background: var(--card);
    border: 1px solid var(--card-edge);
    overflow: hidden;
  }
  .card--back { left: 40px; }
  .card--front { left: 620px; }

  .back-pattern {
    position: absolute;
    inset: 0;
    background:
      linear-gradient(170deg, rgba(255,255,255,0.06) 0%, rgba(0,0,0,0) 40%, rgba(0,0,0,0.25) 100%),
      linear-gradient(100deg, var(--silver) 0%, var(--steel) 22%, var(--graphite) 48%, #1a1a1c 72%, var(--black) 100%);
  }
  .back-brand {
    position: absolute;
    left: 372px;
    top: 128px;
    display: flex;
    align-items: center;
    gap: 6px;
  }
  .back-brand__square { width: 10px; height: 10px; background: var(--red); flex-shrink: 0; }
  .back-brand__name { font-weight: 700; font-size: 11px; color: var(--red); letter-spacing: 0.4px; text-transform: uppercase; white-space: nowrap; }

  .front-brand {
    position: absolute;
    left: 34px;
    top: 128px;
    display: flex;
    align-items: center;
    gap: 10px;
  }
  .front-brand__square { width: 30px; height: 30px; background: var(--red); flex-shrink: 0; }
  .front-brand__name { font-weight: 800; font-size: 19px; color: var(--red); text-transform: uppercase; letter-spacing: 0.5px; line-height: 1.1; }

  .dividers { position: absolute; left: 255px; top: 70px; }

  .contact {
    position: absolute;
    left: 290px;
    top: 48px;
    font-size: 11px;
    line-height: 1.45;
  }
  .contact__name { font-weight: 800; font-size: 19px; color: var(--red); letter-spacing: 0.3px; line-height: 1.1; }
  .contact__title { font-size: 12px; margin-bottom: 10px; }
  .contact__address { margin-bottom: 8px; }
  .contact__row { display: flex; align-items: center; gap: 8px; margin-bottom: 2px; white-space: nowrap; }
  .contact__icon {
    width: 14px; height: 14px; background: var(--red); border-radius: 2px;
    display: flex; align-items: center; justify-content: center; flex-shrink: 0;
  }
</style>
</head>
<body>

<section class="card card--back">
  <div class="back-pattern" role="img" aria-label="Repeating brand mark pattern in rows, fading from silver on the left to glossy black on the right"></div>
  <div class="back-brand">
    <span class="back-brand__square"></span>
    <span class="back-brand__name">Veldmark Supplies</span>
  </div>
</section>

<section class="card card--front">
  <div class="front-brand">
    <span class="front-brand__square"></span>
    <span class="front-brand__name">Veldmark<br>Supplies</span>
  </div>

  <svg class="dividers" width="16" height="170" viewBox="0 0 16 170">
    <line x1="3" y1="0" x2="3" y2="150" stroke="var(--red)" stroke-width="1.2"/>
    <line x1="9" y1="10" x2="9" y2="170" stroke="var(--blue)" stroke-width="1.2"/>
  </svg>

  <div class="contact">
    <p class="contact__name">DARREN HOLLIS</p>
    <p class="contact__title">President</p>
    <p class="contact__address">2450 Ridgeway Blvd, Ste<br>210, Midland, TX 79701</p>
    <p class="contact__row">
      <span class="contact__icon"><svg width="9" height="9" viewBox="0 0 10 10"><path d="M2 1 L4 1 L4.6 3 L3.4 4 Q4.5 6 6 6.6 L7 5.4 L9 6 L9 8 Q5 9 1 3 Z" fill="#fff"/></svg></span>
      432-555-0148
    </p>
    <p class="contact__row">
      <span class="contact__icon"><svg width="9" height="9" viewBox="0 0 10 10"><rect x="2.5" y="0.5" width="5" height="9" rx="1" fill="none" stroke="#fff"/><circle cx="5" cy="8" r="0.6" fill="#fff"/></svg></span>
      432-555-0193
    </p>
    <p class="contact__row">
      <span class="contact__icon"><svg width="9" height="9" viewBox="0 0 10 10"><rect x="0.5" y="2" width="9" height="6" fill="none" stroke="#fff"/><path d="M0.5 2 L5 5.5 L9.5 2" fill="none" stroke="#fff"/></svg></span>
      info@veldmarksupply.net
    </p>
    <p class="contact__row">
      <span class="contact__icon"><svg width="9" height="9" viewBox="0 0 10 10"><circle cx="5" cy="5" r="4" fill="none" stroke="#fff"/><path d="M1 5 H9 M5 1 Q2.5 5 5 9 Q7.5 5 5 1" fill="none" stroke="#fff" stroke-width="0.8"/></svg></span>
      www.veldmarksupply.net
    </p>
  </div>
</section>

</body>
</html>
```